Dental Co needs single page print ad

Dental company needs a 1 page ad for trade magazines.
I am uploading an example of what we want (words). We need you to make it look great. It can include people or not.
The uploaded ad isn't there to be copied, just to kind of frame what we are thinking. We are open to any design
One page ad
Size 1)

Trim Size - 8 x 10.5
Bleed Size - 8.25 x 10.75
Live Area - 7 x 10

Size 2)

Trim - 8 x 10.875
Bleed - 8.25 x 11.125
Live Area - 7 x 9.875

PLUM Brand Hex #'s

Orange - ff6319
Teal - 56b1bf
Lt. Teal - aed9da
Blue: #38394B

Target Market(s)

Dentists

Requirements
Must have
• PLUM Logo, pic of the sensor (called KITE)
Use the brand hex colors:
Orange - ff6319
Teal - 56b1bf
Lt. Teal - aed9da
Blue: #38394B

```html
<!DOCTYPE html>
<html lang="en">
<head>
<meta charset="utf-8">
<title>KITE Intra-Oral Sensor Subscription – PLUM Imaging</title>
<link rel="stylesheet" href="https://fonts.googleapis.com/css2?family=Montserrat:wght@600;700;800;900&family=Fira+Sans:wght@600&family=Tangerine:wght@700&display=swap">
<style>
  :root {
    --orange: #f26722;
    --navy: #2c3481;
    --white: #ffffff;
    --sensor-dark: #1d1f38;
    --sensor-light: #55576a;
  }
  * { box-sizing: border-box; margin: 0; padding: 0; }
  html, body { width: 921px; height: 1200px; overflow: hidden; background: var(--white); }
  .ad {
    position: relative;
    width: 921px;
    height: 1200px;
    overflow: hidden;
    background: var(--white);
    font-family: "Montserrat", Arial, sans-serif;
  }
  .product-name {
    position: absolute;
    top: 62px;
    left: 0;
    width: 100%;
    text-align: center;
    font-family: "Montserrat", Arial, sans-serif;
    font-weight: 900;
    font-size: 134px;
    line-height: 1;
    letter-spacing: -2px;
    color: var(--navy);
  }
  .hero-band {
    position: absolute;
    top: 243px;
    left: 0;
    width: 921px;
    height: 505px;
  }
  .headline {
    position: absolute;
    top: 288px;
    left: 64px;
    font-weight: 800;
    font-size: 57px;
    line-height: 62px;
    color: var(--white);
    letter-spacing: 0.5px;
  }
  .headline-aside {
    position: absolute;
    top: 602px;
    left: 78px;
    font-family: "Tangerine", "Brush Script MT", cursive;
    font-weight: 700;
    font-size: 64px;
    line-height: 1;
    color: var(--navy);
  }
  .pricing {
    position: absolute;
    top: 452px;
    left: 654px;
    width: 220px;
    color: var(--white);
    text-align: center;
  }
  .price-amount {
    font-weight: 700;
    font-size: 66px;
    line-height: 68px;
    letter-spacing: -1px;
  }
  .price-unit { font-size: 30px; letter-spacing: 0; }
  .price-note {
    font-weight: 600;
    font-size: 19.5px;
    line-height: 24px;
  }
  .price-note.large { font-size: 26px; line-height: 28px; }
  .price-block + .price-block { margin-top: 18px; }
  .features {
    position: absolute;
    top: 700px;
    left: 42px;
    display: flex;
    width: 844px;
  }
  .feature {
    width: 168.8px;
    text-align: center;
  }
  .feature-badge {
    width: 96px;
    height: 96px;
    margin: 0 auto;
    border-radius: 50%;
    display: flex;
    align-items: center;
    justify-content: center;
  }
  .feature-badge.navy { background: var(--navy); }
  .feature-badge.orange { background: var(--orange); }
  .feature-label {
    margin-top: 20px;
    font-family: "Fira Sans", Arial, sans-serif;
    font-weight: 600;
    font-size: 18.5px;
    line-height: 22.5px;
    color: var(--navy);
  }
  .contact-bar {
    position: absolute;
    top: 1103px;
    left: 320px;
    width: 601px;
    height: 52px;
    background: var(--orange);
    color: var(--white);
    font-weight: 700;
    font-size: 21.5px;
    line-height: 52px;
    padding-left: 96px;
    letter-spacing: 0.6px;
    word-spacing: 2px;
  }
  .contact-bar .phone { margin-left: 20px; }
  .sensor-photo {
    position: absolute;
    top: 938px;
    left: 82px;
    width: 283px;
    height: 218px;
    border-radius: 30px;
    background: linear-gradient(110deg, var(--sensor-dark) 30%, var(--sensor-light) 100%);
  }
  .brand-name {
    position: absolute;
    top: 962px;
    left: 505px;
    width: 300px;
    text-align: center;
    font-weight: 900;
    color: var(--navy);
    line-height: 1;
  }
  .brand-name .brand-main { display: block; font-size: 78px; letter-spacing: -1px; }
  .brand-name .brand-sub { display: block; font-size: 38px; margin-top: 6px; letter-spacing: 1px; }
</style>
</head>
<body>
<main class="ad">
  <h1 class="product-name">KITE</h1>

  <svg class="hero-band" viewBox="0 0 921 505" aria-hidden="true">
    <rect width="921" height="505" fill="var(--orange)"/>
    <polygon points="690,0 921,0 921,505 533,505" fill="var(--navy)"/>
  </svg>

  <h2 class="headline">A SUBSCRIPTION<br>OPTION FOR<br>INTRA-ORAL<br>SENSORS<br>IS DUMB.</h2>
  <p class="headline-aside">(until you do the math)</p>

  <div class="pricing">
    <div class="price-block">
      <div class="price-amount">$1,999</div>
      <div class="price-note">one-time sign up fee</div>
    </div>
    <div class="price-block">
      <div class="price-amount">$139<span class="price-unit">/mo</span></div>
      <div class="price-note large">cancel anytime</div>
    </div>
  </div>

  <ul class="features" style="list-style:none">
    <li class="feature">
      <div class="feature-badge navy">
        <svg width="58" height="30" viewBox="0 0 58 30" aria-hidden="true"><path d="M29 15 C22 5 6 5 6 15 C6 25 22 25 29 15 C36 5 52 5 52 15 C52 25 36 25 29 15Z" fill="none" stroke="var(--white)" stroke-width="6"/></svg>
      </div>
      <p class="feature-label">Lifetime $0<br>deductible<br>warranty</p>
    </li>
    <li class="feature">
      <div class="feature-badge navy">
        <svg width="60" height="60" viewBox="0 0 60 60" aria-hidden="true">
          <path d="M30 30 C24 22 10 22 10 30 C10 38 24 38 30 30 C36 22 50 22 50 30 C50 38 36 38 30 30Z" fill="none" stroke="var(--white)" stroke-width="3.5"/>
          <rect x="27.5" y="4" width="5" height="14" rx="2" fill="var(--orange)"/>
          <rect x="27.5" y="42" width="5" height="14" rx="2" fill="var(--orange)"/>
        </svg>
      </div>
      <p class="feature-label">Unlimited<br>support &amp;<br>upgrades</p>
    </li>
    <li class="feature">
      <div class="feature-badge navy">
        <svg width="56" height="56" viewBox="0 0 56 56" aria-hidden="true">
          <path d="M30 12 L44 26 L34 36 C28 42 20 42 16 38 C12 34 12 26 18 22Z" fill="var(--white)"/>
          <path d="M30 12 L36 6 L50 20 L44 26Z" fill="var(--orange)"/>
          <line x1="16" y1="38" x2="6" y2="48" stroke="var(--white)" stroke-width="4"/>
          <line x1="40" y1="12" x2="48" y2="4" stroke="var(--orange)" stroke-width="3"/>
        </svg>
      </div>
      <p class="feature-label">Direct<br>integration w/all<br>major software</p>
    </li>
    <li class="feature">
      <div class="feature-badge orange">
        <svg width="54" height="54" viewBox="0 0 54 54" aria-hidden="true">
          <path d="M8 14 L20 6 L48 6 L48 12 L28 12 L20 20Z" fill="var(--white)"/>
          <path d="M46 40 L34 48 L6 48 L6 42 L26 42 L34 34Z" fill="var(--white)"/>
          <circle cx="27" cy="27" r="9" fill="var(--navy)"/>
          <text x="27" y="31.5" text-anchor="middle" font-family="Montserrat, Arial, sans-serif" font-weight="700" font-size="12" fill="var(--white)">$</text>
        </svg>
      </div>
      <p class="feature-label">Affordable<br>enough for<br>every op</p>
    </li>
    <li class="feature">
      <div class="feature-badge orange">
        <svg width="50" height="50" viewBox="0 0 50 50" aria-hidden="true">
          <circle cx="25" cy="6" r="5" fill="var(--navy)"/>
          <ellipse cx="26" cy="28" rx="18" ry="13" fill="var(--white)"/>
          <rect x="15" y="36" width="6" height="8" fill="var(--white)"/>
          <rect x="31" y="36" width="6" height="8" fill="var(--white)"/>
          <rect x="4" y="24" width="6" height="8" rx="2" fill="var(--white)"/>
        </svg>
      </div>
      <p class="feature-label">Preserve<br>your<br>capital</p>
    </li>
  </ul>

  <div class="contact-bar"><span class="web">www.plumimaging.com</span><span class="phone">(555) 234-PLUM</span></div>

  <div class="sensor-photo" role="img" aria-label="Photo of the KITE intra-oral sensor with its cable"></div>

  <div class="brand-name"><span class="brand-main">PLUM</span><span class="brand-sub">IMAGING</span></div>
</main>
</body>
</html>
```